"Harbor Builders" is a residential building company and needs a new business card design and may re

We would like a redesign based on the existing logo, and would like to see a new font as well. We are bespoke home builders who build sustainable energy efficient homes.

Industry/Entity Type

Construction

Contact Information for Business Card

Business card size 40mm x 90mm

Colors

Designer to choose colors to be used in the design.

```html
<!DOCTYPE html>
<html lang="en">
<head>
<meta charset="utf-8">
<title>Harbor Builders – Business Card</title>
<link href="https://fonts.googleapis.com/css2?family=Roboto:wght@400;500&family=Roboto+Condensed:wght@700&display=swap" rel="stylesheet">
<style>
  :root {
    --backdrop: #5b4a3b;
    --ink: #08090b;
    --paper: #f2f2f2;
    --lime: #b5cb2e;
    --white: #ffffff;
  }
  * { margin: 0; padding: 0; box-sizing: border-box; }
  html, body { width: 1200px; height: 960px; overflow: hidden; }
  body { background: var(--backdrop); font-family: "Roboto", Arial, sans-serif; position: relative; }

  .card { position: absolute; width: 600px; height: 343px; overflow: hidden; }
  .card-front { left: 314px; top: 113px; background: var(--paper); }
  .card-back { left: 311px; top: 472px; background: var(--lime); }

  .front-shape { position: absolute; inset: 0; }

  .holder-name {
    position: absolute; left: 36px; top: 38px;
    font-family: "Roboto Condensed", "Arial Narrow", sans-serif;
    font-weight: 700; font-size: 23px; color: var(--lime); letter-spacing: 0.2px;
  }
  .details { position: absolute; left: 36px; top: 150px; color: var(--white); font-size: 14.5px; line-height: 19px; }
  .details .company { font-weight: 500; }
  .details .block { margin-bottom: 5px; }
  .details .registry { padding-left: 1px; }
  .contact { list-style: none; margin-top: 4px; }
  .contact li { display: flex; align-items: center; gap: 8px; height: 19px; }
  .contact svg { width: 14px; height: 14px; flex: none; }

  .brand-name {
    position: absolute; display: flex; align-items: center;
    font-family: "Roboto", Arial, sans-serif; font-weight: 500; white-space: nowrap;
  }
  .brand-front { left: 324px; top: 156px; gap: 10px; font-size: 25px; color: var(--ink); }
  .brand-front .mark { width: 18px; height: 18px; background: var(--lime); }

  .brand-back { left: 0; right: 0; top: 132px; justify-content: center; font-size: 44px; color: var(--white); }

  .website { position: absolute; left: 0; right: 0; top: 298px; text-align: center; color: var(--white); font-size: 14px; letter-spacing: 3px; }
</style>
</head>
<body>
  <section class="card card-front">
    <svg class="front-shape" viewBox="0 0 600 343" aria-hidden="true">
      <polygon points="0,0 354,0 256,170 354,343 0,343" fill="var(--lime)"/>
      <polygon points="0,0 348,0 250,170 348,343 0,343" fill="var(--paper)"/>
      <polygon points="0,0 341,0 244,170 341,343 0,343" fill="var(--ink)"/>
    </svg>
    <h1 class="holder-name">DANIEL MORETTI</h1>
    <div class="details">
      <p class="company">Harbor Builders Pty Ltd</p>
      <p>PO Box 2740 Northgate</p>
      <p class="block">LPO Redcliffe WA 6104</p>
      <p class="registry">Registration 48302</p>
      <p class="registry block">ABN: 42 903 615 278</p>
      <ul class="contact">
        <li><svg viewBox="0 0 14 14"><rect x="3.5" y="0.5" width="7" height="13" rx="1.2" fill="none" stroke="var(--lime)" stroke-width="1.4"/><rect x="5" y="2.5" width="4" height="7" fill="var(--lime)"/></svg>0412 781 336</li>
        <li><svg viewBox="0 0 14 14"><rect x="1" y="3" width="12" height="8" fill="var(--lime)"/><polyline points="1,3 7,8 13,3" fill="none" stroke="var(--ink)" stroke-width="1"/></svg>daniel@harborbuilders.com.au</li>
        <li><svg viewBox="0 0 14 14"><circle cx="7" cy="7" r="6" fill="var(--lime)"/><path d="M4 4c2 1 1 3 3 3s1 3 0 5M9 2c0 2 2 2 3 3" fill="none" stroke="var(--ink)" stroke-width="1"/></svg>www.harborbuilders.com.au</li>
      </ul>
    </div>
    <p class="brand-name brand-front"><span class="mark"></span>Harbor Builders</p>
  </section>

  <section class="card card-back">
    <p class="brand-name brand-back">Harbor Builders</p>
    <p class="website">www.harborbuilders.com.au</p>
  </section>
</body>
</html>
```